MRT Property - Business Cards

Looking for a business card & general letterhead, signage etc design for our new logo.

Colours:
000a20
0056a2
00b5ef
0088ce
68cef2

Fonts:
Poppins
Karla

Please keep look and feel of new brand - example in the zip package I sent.

```html
<!DOCTYPE html>
<html lang="en">
<head>
<meta charset="utf-8">
<title>MRT Property – Business Card</title>
<link rel="stylesheet" href="https://fonts.googleapis.com/css2?family=Poppins:wght@300;400;600;700&display=swap">
<style>
  :root {
    --ink: #000a20;
    --navy: #0056a2;
    --cyan: #00b5ef;
    --mid: #0088ce;
    --sky: #68cef2;
    --paper: #ffffff;
    --backdrop: #d6d6d6;
  }
  * { margin: 0; padding: 0; box-sizing: border-box; }
  html, body { width: 1200px; height: 711px; overflow: hidden; }
  body {
    background: var(--backdrop);
    font-family: "Poppins", sans-serif;
    color: var(--ink);
    position: relative;
  }
  .card {
    position: absolute;
    top: 201px;
    width: 540px;
    height: 309px;
    box-shadow: 0 10px 30px rgba(0,0,0,0.22);
    overflow: hidden;
  }
  .card--front { left: 40px; background: var(--paper); }
  .card--back { left: 620px; }

  .brand {
    position: absolute;
    left: 34px;
    top: 92px;
    display: flex;
    align-items: center;
    gap: 10px;
  }
  .brand__dot {
    width: 22px; height: 22px;
    border-radius: 50%;
    background: var(--sky);
  }
  .brand__name {
    font-weight: 700;
    font-size: 28px;
    color: var(--navy);
    letter-spacing: 0.5px;
  }
  .divider {
    position: absolute;
    left: 268px;
    top: 62px;
    width: 1px;
    height: 150px;
    background: var(--navy);
  }
  .person {
    position: absolute;
    left: 292px;
    top: 70px;
  }
  .person__name {
    font-size: 28px;
    line-height: 1.1;
    white-space: nowrap;
  }
  .person__first { font-weight: 700; color: var(--navy); }
  .person__last { font-weight: 300; color: var(--cyan); }
  .person__role {
    font-size: 12px;
    font-weight: 600;
    color: var(--ink);
    margin-top: 2px;
  }
  .contacts {
    list-style: none;
    margin-top: 16px;
  }
  .contacts li {
    display: flex;
    align-items: center;
    gap: 8px;
    font-size: 12.5px;
    line-height: 20px;
    color: var(--ink);
  }
  .contacts svg { width: 13px; height: 13px; flex: none; }
  .address-band {
    position: absolute;
    left: 0; right: 0;
    top: 240px;
    height: 28px;
    background: var(--navy);
    color: var(--paper);
    font-size: 12px;
    line-height: 28px;
    padding-left: 30px;
    white-space: nowrap;
  }

  .back__pattern {
    position: absolute; inset: 0;
    background: linear-gradient(135deg, #7fd6f5 0%, var(--sky) 50%, #4fc2ee 100%);
  }
  .back__brand {
    position: absolute;
    right: 40px;
    bottom: 52px;
    display: flex;
    align-items: center;
    gap: 6px;
  }
  .back__brand .brand__dot { width: 12px; height: 12px; background: var(--paper); }
  .back__brand .brand__name { font-size: 14px; color: var(--paper); }
</style>
</head>
<body>
  <section class="card card--front" aria-label="Business card front">
    <div class="brand">
      <span class="brand__dot"></span>
      <span class="brand__name">MRT Property</span>
    </div>

    <div class="divider"></div>

    <div class="person">
      <p class="person__name"><span class="person__first">Callum</span> <span class="person__last">Reid</span></p>
      <p class="person__role">Director</p>
      <ul class="contacts">
        <li>
          <svg viewBox="0 0 24 24" fill="none" stroke="#00b5ef" stroke-width="2.4" stroke-linecap="round" stroke-linejoin="round"><path d="M22 16.9v3a2 2 0 0 1-2.2 2 19.8 19.8 0 0 1-8.6-3.1 19.5 19.5 0 0 1-6-6A19.8 19.8 0 0 1 2.1 4.2 2 2 0 0 1 4.1 2h3a2 2 0 0 1 2 1.7c.1 1 .4 1.9.7 2.8a2 2 0 0 1-.5 2.1L8 9.9a16 16 0 0 0 6 6l1.3-1.3a2 2 0 0 1 2.1-.4c.9.3 1.8.6 2.8.7a2 2 0 0 1 1.8 2z"/></svg>
          +61 2 9000 4821
        </li>
        <li>
          <svg viewBox="0 0 24 24" fill="none" stroke="#00b5ef" stroke-width="2.4"><circle cx="12" cy="12" r="10"/><path d="M2 12h20M12 2a15 15 0 0 1 0 20M12 2a15 15 0 0 0 0 20"/></svg>
          www.mrtproperty.com.au
        </li>
        <li>
          <svg viewBox="0 0 24 24" fill="none" stroke="#00b5ef" stroke-width="2.4" stroke-linejoin="round"><rect x="2" y="5" width="20" height="14" rx="2"/><path d="M2 7l10 7 10-7"/></svg>
          info@mrtproperty.com.au
        </li>
      </ul>
    </div>

    <div class="address-band">Suite 3.04, Level 2 18 Harbour Lane Rhodes Park NSW 2138</div>
  </section>

  <section class="card card--back" aria-label="Business card back">
    <div class="back__pattern" role="img" aria-label="Repeating brand pattern in light and mid blue tones"></div>
    <div class="back__brand">
      <span class="brand__dot"></span>
      <span class="brand__name">MRT Property</span>
    </div>
  </section>
</body>
</html>
```